Envelope Design - Winner can do follow-up business

- Varnoko.com is a Swiss-based online store selling business shirts and accessories for business men
- Please visit the webpage to make yourself familiar with the company. Although the text is in German, with Plimbo translator you should be able to understand the main content.
- Our clients are mainly business men between 30 and 60 years old. Mostly with a high income working in the service industry (banking, insurance, lawyers, etc.). Sometimes there wives purchase the shirts for them ;-)
- The colors and the logo are given, as they are also used for the print materials (please see files in attachment)
- I am running several businesses and often need a talented web designer --> the winner gets substantial follow-up business
your task:
-for our company we need a new envelope design
-It should be simple and modern
-please use one of the logos in the followings.
-suprise me :)

```html
<!DOCTYPE html>
<html lang="en">
<head>
<meta charset="utf-8">
<title>Varnoko Envelope Set</title>
<link rel="stylesheet" href="https://fonts.googleapis.com/css2?family=Krona+One&family=Open+Sans:wght@400&display=swap">
<style>
  :root {
    --backdrop: #ece9e4;
    --paper: #ffffff;
    --edge: #b9b9b9;
    --red: #ee2e24;
    --gold: #e6d66a;
    --gold-faint: #efe39a;
    --black: #000000;
    --grey: #8d8d8d;
    --ink-light: #ffffff;
  }
  * { margin: 0; padding: 0; box-sizing: border-box; }
  html, body { width: 1200px; height: 962px; overflow: hidden; }
  body { background: var(--backdrop); position: relative; font-family: "Open Sans", Arial, sans-serif; }

  .envelope {
    position: absolute;
    width: 975px;
    height: 460px;
    background: var(--paper);
    border: 1px solid var(--edge);
    overflow: hidden;
  }
  .envelope svg { position: absolute; left: 0; top: 0; }
  .envelope--back   { left: 180px; top: 47px; }
  .envelope--middle { left: 89px;  top: 237px; }
  .envelope--front  { left: 35px;  top: 447px; }

  .wordmark {
    position: absolute;
    font-family: "Krona One", "Arial Black", sans-serif;
    letter-spacing: 1px;
    white-space: nowrap;
  }
  .flap-name { top: 52px; left: 345px; font-size: 36px; color: var(--gold); }
  .flap-name--faint { top: 52px; left: 405px; font-size: 28px; color: var(--gold-faint); }

  .front-band {
    position: absolute; left: 0; top: 0; width: 100%; height: 108px;
    background: var(--black);
  }
  .band-brand {
    position: absolute; left: 32px; top: 12px;
    display: flex; flex-direction: column; align-items: center; gap: 14px;
  }
  .band-brand .mark-square { width: 24px; height: 24px; background: var(--gold); }
  .band-brand .wordmark { position: static; font-size: 30px; color: var(--gold); }
  .band-side-name { right: 14px; top: 40px; font-size: 20px; color: var(--grey); }

  .contact {
    position: absolute; left: 0; width: 100%;
    color: var(--ink-light); font-size: 20px;
    display: flex; justify-content: center; align-items: center; gap: 10px;
  }
  .contact svg { position: static; }
  .contact--web { top: 390px; padding-left: 25px; }
  .contact--address { top: 423px; padding-left: 0; }
</style>
</head>
<body>

  <!-- back envelope: red flap -->
  <div class="envelope envelope--back">
    <svg width="975" height="460" viewBox="0 0 975 460">
      <path d="M0 0 H975 C965 30 960 65 930 80 C905 92 880 88 850 92 L530 150 C505 155 465 155 445 150 L110 88 C80 82 50 84 30 70 C10 55 8 25 0 0 Z" fill="var(--red)"/>
    </svg>
    <div class="wordmark flap-name">VARNOKO</div>
  </div>

  <!-- middle envelope: gold flap -->
  <div class="envelope envelope--middle">
    <svg width="975" height="460" viewBox="0 0 975 460">
      <path d="M0 0 H975 C965 30 960 65 930 80 C905 92 880 88 850 92 L520 148 C495 153 455 153 435 148 L110 88 C80 82 50 84 30 70 C10 55 8 25 0 0 Z" fill="var(--gold)"/>
    </svg>
    <div class="wordmark flap-name--faint">VARNOKO</div>
  </div>

  <!-- front envelope -->
  <div class="envelope envelope--front">
    <div class="front-band">
      <div class="band-brand">
        <span class="mark-square"></span>
        <span class="wordmark">VARNOKO</span>
      </div>
      <div class="wordmark band-side-name">VARNOKO</div>
    </div>

    <svg width="975" height="460" viewBox="0 0 975 460">
      <path d="M0 418 Q487 320 975 418" fill="none" stroke="var(--gold)" stroke-width="4"/>
      <path d="M0 425 Q487 335 975 425 V460 H0 Z" fill="var(--paper)"/>
      <path d="M0 425 Q487 348 975 425 V460 H0 Z" fill="var(--red)"/>
    </svg>

    <div class="contact contact--web">
      <svg width="22" height="22" viewBox="0 0 22 22" aria-hidden="true">
        <g fill="none" stroke="#fff" stroke-width="1.4">
          <circle cx="11" cy="11" r="9.5"/>
          <ellipse cx="11" cy="11" rx="4.2" ry="9.5"/>
          <line x1="1.5" y1="11" x2="20.5" y2="11"/>
          <path d="M3.5 6 H18.5 M3.5 16 H18.5"/>
        </g>
      </svg>
      <span>www.varnoko.com</span>
    </div>
    <div class="contact contact--address">
      <svg width="18" height="24" viewBox="0 0 18 24" aria-hidden="true">
        <path d="M9 0 C4 0 0 4 0 9 C0 15 9 24 9 24 C9 24 18 15 18 9 C18 4 14 0 9 0 Z M9 5 A4 4 0 1 1 9 13 A4 4 0 1 1 9 5 Z" fill="#fff" fill-rule="evenodd"/>
      </svg>
      <span>Street Name, City Name, State Zipcode</span>
    </div>
  </div>

</body>
</html>
```